Growing the Ironclad Young Contender:
A Family Playbook for Nurturing Bold, Grounded, and Resilient Daughters at Games and Beyond.
📘 Book Cover Design Brief – “Growing the Ironclad Young Contender”

Project Title:
Design a bold, inspiring book cover for a best-selling book titled:
Growing the Ironclad Young Contender
Subtitle: A Family Playbook for Nurturing Bold, Grounded, and Resilient Daughters at Games and Beyond

🎯 Audience:

Parents of female athletes ages 14–20 who want their daughters to build confidence, strength, resilience, and long-term success both in sports and in life.

This book should feel encouraging, empowering, and credible — NOT cheesy, childish, or overly academic.

📕 Design Tone & Style:

Powerful and professional — should feel like a best-selling book from a leading performance or parenting expert

Emotionally compelling — conveys hope, resilience, strength, and possibility

Visually modern and clean — avoid anything overly busy, cliché, or childish

Heroic/aspirational tone — think transformation, leadership, strong positioning

💡 Visual Direction / Ideas (Use as Inspiration, Not Limitation):

Strong, confident teenage YOUNG CONTENDER imagery — adaptable beyond one specific sport

Symbolic visuals — e.g. athlete standing strong, on a starting line, looking bold into the future, silhouette, or power stance

Bold typography that feels clean and modern (e.g., Proxima Nova, Montserrat, Gotham, Bebas Neue, etc.)

A title that stands out clearly when viewed as a thumbnail on Brindlemart

Color tones: Empowering, modern, and strong: think deep blues, greens, purples, or golds — avoid playful pastels or overly girly themes

Potential imagery: textured backgrounds, motion, bravery, development, strength, growth, sport/action overlays

🔥 What the Cover MUST Communicate:

✅ This is for parents who want strong, confident female athletes
✅ It’s a guidebook for personal development AND sports performance
✅ It’s about creating “IRONCLAD” confidence — physically, mentally and emotionally
✅ The message is: You can help your daughter become her strongest, most confident self

📚 Back-of-Book Summary (for context):

"Growing the Ironclad Young Contender" is a parent's blueprint to building girls who are strong in body, confident in mind, and ready to lead on and off the field. Through simple strategies around strength training, mindset, nutrition, and character development, this book gives parents the tools to help their daughters stay injury-resistant, break through mental barriers, and unlock their full potential — in sports and in life.

✅ Deliverables:

Full cover design (front, back, spine) for paperback
High-resolution files (print-ready)
Source files (PSD, AI, etc.)
3D mockup versions of the book (standing, flat, stack)

Target Market(s)

Industry/Entity Type

Fitness

Font styles to use
Sans Serif

Colors
FFF300
FFF600
FEFA6F
FFFEC7
FFFEE8

Requirements
Must have
• Bold Font
Should not have
• I don't want an image of a YOUNG CONTENDER. I want this to be font based.

```html
<!DOCTYPE html>
<html lang="en">
<head>
<meta charset="utf-8">
<title>Growing the Ironclad Young Contender – Book Cover</title>
<link rel="stylesheet" href="https://fonts.googleapis.com/css2?family=Bebas+Neue&family=Oswald:wght@500;600&display=swap">
<style>
  :root {
    --page-bg: #ececec;
    --cover-black: #0b0b0b;
    --cover-charcoal: #1c1c1c;
    --ink-white: #ffffff;
    --gold: #b8a25a;
    --gold-deep: #a88f48;
    --gold-light: #eee5a9;
  }
  html, body {
    margin: 0;
    width: 1200px;
    height: 1200px;
    overflow: hidden;
    background: var(--page-bg);
  }
  .book-cover {
    position: absolute;
    left: 256px;
    top: 84px;
    width: 688px;
    height: 1032px;
    background:
      radial-gradient(ellipse at 70% 8%, rgba(60,60,60,0.45), transparent 55%),
      radial-gradient(ellipse at 20% 70%, rgba(40,40,40,0.4), transparent 60%),
      var(--cover-black);
  }
  .cover-art { display: block; width: 688px; height: 1032px; }
  .subtitle {
    font-family: "Oswald", sans-serif;
    font-weight: 600;
    font-size: 22px;
  }
  .title-line {
    font-family: "Bebas Neue", "Oswald", sans-serif;
    fill: var(--ink-white);
  }
  .tone-gold { fill: var(--gold); }
  .tone-white { fill: var(--ink-white); }
  .brand-name {
    font-family: "Oswald", sans-serif;
    font-weight: 600;
    font-size: 20px;
    letter-spacing: 2px;
    fill: var(--ink-white);
  }
  .brand-tag {
    font-family: "Oswald", sans-serif;
    font-weight: 500;
    font-size: 11px;
    letter-spacing: 3px;
    fill: var(--ink-white);
  }
</style>
</head>
<body>
  <div class="book-cover">
    <svg class="cover-art" viewBox="0 0 688 1032" xmlns="http://www.w3.org/2000/svg">
      <defs>
        <linearGradient id="goldSheen" x1="0" y1="0" x2="1" y2="0">
          <stop offset="0" stop-color="#b39b52"/>
          <stop offset="0.5" stop-color="#efe6ad"/>
          <stop offset="1" stop-color="#b39b52"/>
        </linearGradient>
        <radialGradient id="athleteGlow" cx="0.5" cy="0.5" r="0.5">
          <stop offset="0" stop-color="#b8a25a" stop-opacity="0.55"/>
          <stop offset="1" stop-color="#b8a25a" stop-opacity="0.12"/>
        </radialGradient>
      </defs>

      <!-- subtitle -->
      <text class="subtitle" x="87" y="69" textLength="528" lengthAdjust="spacingAndGlyphs">
        <tspan class="tone-gold">A FAMILY PLAYBOOK FOR NURTURING </tspan><tspan class="tone-white">BOLD, GROUNDED,</tspan>
      </text>
      <text class="subtitle" x="127" y="97" textLength="448" lengthAdjust="spacingAndGlyphs">
        <tspan class="tone-white">AND RESILIENT </tspan><tspan class="tone-gold">DAUGHTERS AT GAMES AND BEYOND</tspan>
      </text>

      <!-- action figure area -->
      <rect x="221" y="410" width="290" height="453" rx="40" fill="url(#athleteGlow)"
            role="img" aria-label="Gold silhouette of a young basketball player leaping for a layup"/>

      <!-- title -->
      <text class="title-line" x="87" y="217" font-size="145" textLength="524" lengthAdjust="spacingAndGlyphs">GROWING THE</text>
      <text class="title-line" x="42" y="335" font-size="146" textLength="614" lengthAdjust="spacingAndGlyphs" fill="url(#goldSheen)" style="fill:url(#goldSheen)">IRONCLAD</text>
      <text class="title-line" x="89" y="516" font-size="238" textLength="522" lengthAdjust="spacingAndGlyphs">YOUNG</text>
      <text class="title-line" x="89" y="683" font-size="219" textLength="520" lengthAdjust="spacingAndGlyphs">CONTENDER</text>

      <!-- publisher brand -->
      <circle cx="346" cy="908" r="40" fill="none" stroke="var(--gold)" stroke-width="4"/>
      <text class="brand-name" x="344" y="978" text-anchor="middle" textLength="228" lengthAdjust="spacingAndGlyphs">IRONCLAD</text>
      <line x1="231" y1="987" x2="256" y2="987" stroke="var(--ink-white)" stroke-width="1.2"/>
      <text class="brand-tag" x="344" y="991" text-anchor="middle" textLength="160" lengthAdjust="spacingAndGlyphs">YOUNG CONTENDER</text>
      <line x1="433" y1="987" x2="458" y2="987" stroke="var(--ink-white)" stroke-width="1.2"/>
    </svg>
  </div>
</body>
</html>
```